SkyvornQ Business Cards and Stationary Design

Need a design for our business cards and stationary. I want to carry on the theme of the logo. I want the business cards to have a design on the back. I would like the business cards and the stationary to carry the same theme, design scheme, and branding

Target Market(s)

Airlines and Maintenance Facilities

Industry/Entity Type

Aviation

Contact Information for Business Card

Name
Position Title
Address: 4827 Trellis Hollow Road, Fort Pierce, Florida, 34951
Office Number
Mobile Number
Email
Website

Font styles to use
Serif
Sans Serif

Colors

Designer to choose colors to be used in the design.

```html
<!DOCTYPE html>
<html lang="en">
<head>
<meta charset="utf-8">
<title>SkyvornQ Business Card</title>
<link rel="stylesheet" href="https://fonts.googleapis.com/css2?family=Source+Sans+3:wght@400;600;700&display=swap">
<style>
  :root {
    --backdrop-top: #e7e8e9;
    --backdrop-bottom: #cfd1d3;
    --navy: #1b2c58;
    --navy-deep: #13244d;
    --blue: #2178b8;
    --blue-bright: #2a9ad6;
    --blue-edge: #22508a;
    --white: #ffffff;
    --card-edge: #2b2b2b;
  }
  * { margin: 0; padding: 0; box-sizing: border-box; }
  html, body { width: 1200px; height: 1102px; overflow: hidden; }
  body {
    position: relative;
    background: linear-gradient(160deg, var(--backdrop-top), var(--backdrop-bottom));
    font-family: "Source Sans 3", sans-serif;
  }
  .card {
    position: absolute;
    width: 789px;
    height: 450px;
    border-radius: 38px;
    overflow: hidden;
  }
  .card-front {
    left: 338px; top: 68px;
    background: var(--white);
    border: 1px solid var(--card-edge);
  }
  .card-front .swoosh { position: absolute; inset: 0; width: 100%; height: 100%; }
  .brand-mark {
    position: absolute;
    left: 178px; top: 32px;
    width: 122px; height: 122px;
    border: 8px solid var(--navy);
    border-radius: 50%;
  }
  .brand-name {
    position: absolute;
    left: 56px; top: 172px;
    font-size: 50px;
    font-weight: 700;
    letter-spacing: 9px;
    color: var(--navy);
    line-height: 1;
  }
  .holder { position: absolute; left: 56px; top: 268px; color: var(--navy); }
  .holder-name { font-size: 29px; font-weight: 700; letter-spacing: 0.5px; line-height: 1.2; }
  .holder-title { font-size: 25px; font-weight: 400; color: #2a2f3e; line-height: 1.3; }
  .contact {
    position: absolute;
    right: 33px; top: 246px;
    list-style: none;
    color: var(--white);
    font-size: 19px;
    text-align: right;
    line-height: 27.5px;
  }
  .contact li { display: flex; justify-content: flex-end; align-items: center; gap: 6px; }
  .contact .gap { margin-top: 14px; }
  .contact svg { width: 17px; height: 17px; flex: none; }
  .card-back {
    left: 85px; top: 568px;
    background: radial-gradient(ellipse at 50% 45%, var(--blue-bright) 0%, var(--blue) 45%, var(--blue-edge) 100%);
  }
  .back-ring {
    position: absolute;
    left: 276px; top: 60px;
    width: 262px; height: 262px;
    border: 12px solid var(--navy);
    border-radius: 50%;
  }
  .back-name {
    position: absolute;
    left: 0; right: 0; top: 166px;
    text-align: center;
    font-size: 50px;
    font-weight: 700;
    letter-spacing: 6px;
    color: var(--white);
    line-height: 1;
  }
  .back-web {
    position: absolute;
    left: 0; right: 0; top: 360px;
    text-align: center;
    color: var(--white);
    font-size: 25px;
    letter-spacing: 6.5px;
  }
</style>
</head>
<body>
  <section class="card card-front">
    <svg class="swoosh" viewBox="0 0 841 480" preserveAspectRatio="none" aria-hidden="true">
      <defs>
        <radialGradient id="frontBlue" cx="0.6" cy="0.85" r="0.6">
          <stop offset="0" stop-color="#2a86c8"/>
          <stop offset="1" stop-color="#1f3468"/>
        </radialGradient>
      </defs>
      <path d="M0,408 C250,462 590,400 841,16 V480 H0 Z" fill="url(#frontBlue)"/>
      <path d="M0,352 C150,425 420,425 590,262 C420,392 180,432 0,396 Z" fill="#13244d"/>
    </svg>
    <div class="brand-mark"></div>
    <div class="brand-name">SKYVORNQ</div>
    <div class="holder">
      <div class="holder-name">DARREN KOLBECK</div>
      <div class="holder-title">PRESIDENT</div>
    </div>
    <ul class="contact">
      <li><svg viewBox="0 0 20 20"><circle cx="10" cy="10" r="8.5" fill="none" stroke="#fff" stroke-width="1.6"/><path d="M6.5 5.5l2 0 .8 2.4-1.2 1c.6 1.3 1.4 2.1 2.6 2.7l1-1.2 2.4.8v2c-4.5.3-8-3.3-7.6-7.7z" fill="#fff"/></svg>012-345-6789</li>
      <li><svg viewBox="0 0 20 20"><circle cx="10" cy="10" r="8.5" fill="none" stroke="#fff" stroke-width="1.6"/><rect x="7" y="5" width="6" height="10" rx="1" fill="none" stroke="#fff" stroke-width="1.4"/></svg>012-345-6789</li>
      <li><svg viewBox="0 0 20 20"><circle cx="10" cy="10" r="8.5" fill="none" stroke="#fff" stroke-width="1.6"/><rect x="5.5" y="7" width="9" height="6.5" fill="none" stroke="#fff" stroke-width="1.3"/><path d="M5.5 7l4.5 3.5 4.5-3.5" fill="none" stroke="#fff" stroke-width="1.3"/></svg>info@skyvornq.com</li>
      <li><svg viewBox="0 0 20 20"><circle cx="10" cy="10" r="8.5" fill="none" stroke="#fff" stroke-width="1.6"/><ellipse cx="10" cy="10" rx="3.5" ry="8.5" fill="none" stroke="#fff" stroke-width="1.2"/><path d="M1.5 10h17M3 6h14M3 14h14" stroke="#fff" stroke-width="1.2"/></svg>www.skyvornq.com</li>
      <li class="gap"><svg viewBox="0 0 20 20"><circle cx="10" cy="10" r="8.5" fill="none" stroke="#fff" stroke-width="1.6"/><path d="M10 15s-3.5-3.8-3.5-6.2a3.5 3.5 0 017 0C13.5 11.2 10 15 10 15z" fill="none" stroke="#fff" stroke-width="1.3"/><circle cx="10" cy="8.8" r="1.2" fill="#fff"/></svg>4827 Trellis Hollow Road, Fort Pierce,</li>
      <li>Florida, 34951</li>
    </ul>
  </section>

  <section class="card card-back">
    <div class="back-ring"></div>
    <div class="back-name">SKYVORNQ</div>
    <div class="back-web">www.skyvornq.com</div>
  </section>
</body>
</html>
```